Brindle Sky Port needs a new upscale business card design for our high end aircraft hangar complex

Brindle Sky Port (BSP) is a large, upscale jet hangar complex in the US housing expensive aircraft. We need a new business card design, using our current logo. We will be attending a industry convention and need a card design that will stand out and be remembered by aircraft owners and private pilots.

Target Market(s)

Aircraft pilots or owners looking for a new upscale hangar

Industry/Entity Type

Airport

Contact Information for Business Card

I like to use very heavy card stock, 400#, double sided. Square, no rounded edges please.

Colors
3276b5
0255a3
85abd2

Requirements
Must have
• An expensive, classy design, vivid colors.
Nice to have
• Needs to look very expensive and classy, and have some "pop". Designer must be able to download or copy my current typeface or fonts.
• One card side might be black with the "Logo and Brindle Sky Port Double line image in blue (or try gold, or glossy black), and perhaps have a grayed out "K720 jet silhouette". The other card side would have our contact info, and perhaps the "BSP Logo only". I'd like my contact info 'stacked', not in a paragraph format.
Should not have
• Should not look "too busy". Having a double-sided card will help.

```html
<!DOCTYPE html>
<html lang="en">
<head>
<meta charset="utf-8">
<title>Brindle Sky Port – Business Card</title>
<link href="https://fonts.googleapis.com/css2?family=Montserrat:wght@400;600;700&display=swap" rel="stylesheet">
<style>
  :root {
    --page: #e9ebee;
    --card: #ffffff;
    --navy: #11396b;
    --brand: #1f5a96;
    --ink-light: #ffffff;
    --ink-soft: #c9d7e8;
    --sky-top: #f4f5f7;
    --sky-mid: #c9ccd1;
  }
  * { margin: 0; padding: 0; box-sizing: border-box; }
  html, body { width: 1200px; height: 900px; overflow: hidden; }
  body {
    background: var(--page);
    font-family: "Montserrat", sans-serif;
    position: relative;
  }
  .card {
    position: absolute;
    width: 700px;
    height: 400px;
    background: var(--card);
    box-shadow: 0 10px 28px rgba(0,0,0,0.18);
    overflow: hidden;
  }
  .card--front { left: 80px; top: 40px; }
  .card--back { left: 420px; top: 460px; }

  .brand-name {
    position: absolute;
    z-index: 1;
    display: flex;
    align-items: center;
    gap: 12px;
    color: var(--brand);
    font-weight: 700;
    font-size: 30px;
    line-height: 1.05;
    text-transform: uppercase;
    letter-spacing: 0.5px;
    white-space: nowrap;
  }
  .brand-name .brand-mark {
    width: 16px; height: 16px; background: var(--brand); flex: none;
  }
  .card--front .brand-name { left: 44px; top: 150px; }

  .jet-photo {
    position: absolute;
    left: 270px; top: 40px;
    width: 380px; height: 270px;
    background: radial-gradient(ellipse at 50% 55%, var(--sky-mid) 0%, #e2e4e7 40%, var(--sky-top) 72%, rgba(255,255,255,0) 100%);
  }
  .front-web {
    position: absolute;
    right: 40px; bottom: 42px;
    color: var(--navy);
    font-size: 15px;
    letter-spacing: 0.3px;
  }

  .card--back .brand-name { left: 44px; top: 170px; }
  .contact-panel {
    position: absolute;
    left: 290px; top: 0;
    width: 410px; height: 400px;
    background: var(--navy);
    color: var(--ink-light);
    padding: 125px 0 0 70px;
  }
  .contact-panel::before {
    content: "";
    position: absolute;
    left: 0; top: 150px;
    border-top: 14px solid transparent;
    border-bottom: 14px solid transparent;
    border-left: 14px solid var(--card);
  }
  .person-name { font-size: 24px; font-weight: 600; }
  .person-role { font-size: 14px; color: var(--ink-soft); margin: 2px 0 16px 20px; }
  .contact-list { list-style: none; }
  .contact-list li {
    display: flex; align-items: center; gap: 14px;
    font-size: 15px; line-height: 22px; margin-left: 20px;
  }
  .contact-list svg { width: 12px; height: 12px; flex: none; }
</style>
</head>
<body>

  <section class="card card--front">
    <div class="jet-photo" role="img" aria-label="Photograph of a private K720 jet seen head-on against white"></div>
    <div class="brand-name"><span class="brand-mark"></span><span>Brindle<br>Sky Port</span></div>
    <p class="front-web">www.brindleskyport.com</p>
  </section>

  <section class="card card--back">
    <div class="brand-name"><span class="brand-mark"></span><span>Brindle<br>Sky Port</span></div>
    <div class="contact-panel">
      <h1 class="person-name">Corin Haldane</h1>
      <p class="person-role">Director</p>
      <ul class="contact-list">
        <li><svg viewBox="0 0 12 12"><path d="M2 1 L4 1 L5 4 L3.6 5 Q4.8 7.4 7 8.4 L8 7 L11 8 L11 10 Q11 11 10 11 Q2 10.5 1 2 Q1 1 2 1Z" fill="currentColor"/></svg>+033 2719-4052</li>
        <li><svg viewBox="0 0 12 12"><path d="M1 4 Q6 0 11 4 L9.5 5.5 L8 4.5 L8 3.5 Q6 2.6 4 3.5 L4 4.5 L2.5 5.5Z M3 7 H9 V11 H3Z" fill="currentColor"/></svg>+033 2583-6104</li>
        <li><svg viewBox="0 0 12 12"><rect x="1" y="2.5" width="10" height="7" fill="none" stroke="currentColor" stroke-width="1.2"/><path d="M1 2.5 L6 6.5 L11 2.5" fill="none" stroke="currentColor" stroke-width="1.2"/></svg>info@brindleskyport.com</li>
        <li><svg viewBox="0 0 12 12"><circle cx="6" cy="6" r="5" fill="none" stroke="currentColor" stroke-width="1.1"/><ellipse cx="6" cy="6" rx="2.2" ry="5" fill="none" stroke="currentColor" stroke-width="1"/><path d="M1 6 H11" stroke="currentColor" stroke-width="1"/></svg>www.brindleskyport.com</li>
      </ul>
    </div>
  </section>

</body>
</html>
```